Velmarsh Group Webpage Design

We need a new website for our company. The company is Velmarsh Group Pty Ltd. We are in the business of Asbestos Removal; Demolition; Earthworks and Transport. We do not advertise and would like our website to be a reference point for our clients / potential clients and also to make our services known to those searching the internet for the services we offer. Some examples of the style of website we are after are:
http://www.quarnedemolition-example.com.au/
http://m.brintowerdemolitions-example.com.au/
http://www.fenwarddemolition-example.com.au
http://www.tolvik-example.com.au
http://www.ptrservices-example.com.au
http://www.steadfast-dismantling-example.com.au
We will need to work on content. Enclosed is an example. We also need to purchase the domain velmarshgroup-example.com.au and need to set up email accounts and ensure the website is mobile friendly. We have a company logo and have built our business on delivering professional, quality services on time. We would like the webpage to be simple, informative and professional - black and white / grey themed. We would also like to add a photo gallery etc later.

Industry/Entity Type

Construction

Coding

Coded - Design and coding required

Number of Pages Required

1 page

Colors
000000
fcfcfc
959595
dddddd

Requirements
Must have
• Information regarding the services we provide

```html
<!DOCTYPE html>
<html lang="en">
<head>
<meta charset="utf-8">
<title>Velmarsh Group</title>
<link href="https://fonts.googleapis.com/css2?family=Michroma&family=Jura:wght@400;500&family=Roboto+Condensed:wght@400&family=Open+Sans:wght@400;700&display=swap" rel="stylesheet">
<style>
:root{
  --ink:#231f20;
  --black:#000000;
  --white:#fcfcfc;
  --grey:#959595;
  --light:#dddddd;
  --body-text:#555555;
  --rule:#3d393a;
}
*{margin:0;padding:0;box-sizing:border-box}
html,body{width:1037px;height:1200px;overflow:hidden;background:var(--white)}
body{position:relative;font-family:"Open Sans",sans-serif}
.site-header{position:absolute;left:0;top:0;width:1037px;height:88px;background:var(--ink)}
.brand{position:absolute;left:67px;top:20px;color:var(--white);font-family:"Michroma",sans-serif;font-size:26px;letter-spacing:3px;line-height:1}
.brand small{display:block;font-size:9px;letter-spacing:12px;text-align:center;margin-top:8px;color:var(--white)}
.main-nav{position:absolute;left:432px;top:27px;display:flex;font-family:"Roboto Condensed",sans-serif;font-size:17px}
.main-nav a{color:var(--light);text-decoration:none;height:40px;line-height:40px;padding:0 15px}
.main-nav a.active{background:var(--black);color:var(--white);padding:0 20px}
.hero{position:absolute;left:0;top:88px;width:1037px;height:576px;overflow:hidden}
.hero-photo{position:absolute;inset:0;background:linear-gradient(180deg,#7e8c99 0%,#c5ccd3 35%,#a69c8c 62%,#c9bfb7 100%)}
.hero-bands{position:absolute;inset:0}
.tagline{position:absolute;left:342px;top:32px;height:110px;border-left:2px solid var(--ink);padding-left:21px;padding-top:44px;font-family:"Michroma",sans-serif;font-size:18.5px;line-height:1;color:var(--black);white-space:nowrap}
.tagline span{margin:0 12px;font-size:12px;vertical-align:middle}
.services{position:absolute;left:267px;top:410px;display:flex;gap:18px}
.service-card{width:162px;height:129px;border:1px solid var(--black);background:var(--black);overflow:hidden}
.service-card .thumb{height:92px}
.service-card h3{height:36px;line-height:36px;text-align:center;color:var(--white);font-family:"Jura",sans-serif;font-weight:500;font-size:16px;letter-spacing:.3px;white-space:nowrap}
.welcome{position:absolute;left:0;top:664px;width:1037px;height:266px;text-align:center}
.welcome h1{margin-top:44px;font-family:"Michroma",sans-serif;font-weight:400;font-size:27px;color:var(--black);letter-spacing:-.5px;white-space:nowrap}
.welcome h1 b{font-size:28px;letter-spacing:1px}
.welcome p{width:720px;margin:20px auto 0;font-size:14px;line-height:22px;color:var(--body-text)}
.btn{display:inline-block;margin-top:20px;background:var(--ink);color:var(--white);font-family:"Jura",sans-serif;font-weight:500;font-size:20px;padding:0 20px;height:41px;line-height:41px;text-decoration:none}
.site-footer{position:absolute;left:0;top:930px;width:1037px;height:270px;background:var(--ink);color:var(--white)}
.footer-col{position:absolute;top:20px;height:180px}
.footer-col h2{font-family:"Jura",sans-serif;font-weight:500;font-size:21px;color:var(--white);letter-spacing:.3px}
.col-links{left:68px}
.col-contact{left:359px;padding-left:26px;border-left:1px solid var(--rule);width:318px}
.col-follow{left:677px;padding-left:24px;border-left:1px solid var(--rule);width:294px}
.col-links ul{list-style:none;margin-top:10px}
.col-links li{font-size:14px;line-height:27px;padding-left:18px;position:relative}
.col-links li::before{content:"";position:absolute;left:6px;top:10px;width:6px;height:6px;border-radius:50%;background:var(--white)}
.contact-row{display:flex;gap:14px;margin-top:14px;font-size:14px;line-height:21px}
.contact-row svg{flex:none;margin-top:2px}
.social{display:flex;gap:46px;margin-top:22px}
.social span{width:16px;height:16px;border-radius:50%;background:var(--white)}
.footer-brand{margin-top:32px;font-family:"Michroma",sans-serif;font-size:25px;letter-spacing:3px;color:#4a4647}
.footer-base{position:absolute;left:66px;top:223px;width:905px;border-top:1px solid var(--rule);text-align:center;padding-top:14px;font-size:14px;color:var(--grey)}
.footer-base b{color:var(--white)}
</style>
</head>
<body>
<header class="site-header">
  <div class="brand">VELMARSH<small>GROUP</small></div>
  <nav class="main-nav">
    <a class="active" href="#">HOME</a><a href="#">ABOUT</a><a href="#">SERVICES</a><a href="#">SAFETY</a><a href="#">ENVIRONMENT</a><a href="#">CONTACT</a>
  </nav>
</header>

<section class="hero">
  <div class="hero-photo" role="img" aria-label="Yellow bulldozer and dump truck working at an open quarry under a cloudy sky"></div>
  <svg class="hero-bands" width="1037" height="576" viewBox="0 0 1037 576">
    <polygon points="0,0 300,0 0,360" fill="#1c1a1b" opacity=".85"/>
    <polygon points="0,0 90,0 0,110" fill="#2e2b2c"/>
    <polygon points="1037,170 1037,576 700,576" fill="#1c1a1b" opacity=".7"/>
    <polygon points="1037,330 1037,576 860,576" fill="#2e2b2c" opacity=".6"/>
  </svg>
  <div class="tagline">TRANSPORT<span>●</span>DEMOLITION<span>●</span>EARTHMOVING</div>
  <div class="services">
    <article class="service-card"><div class="thumb" role="img" aria-label="Excavator breaking up a concrete roadway" style="background:linear-gradient(180deg,#5a8fd0,#b7a98a)"></div><h3>Demolition</h3></article>
    <article class="service-card"><div class="thumb" role="img" aria-label="Wheel loader moving earth" style="background:linear-gradient(180deg,#6f8a6a,#5b5346)"></div><h3>Earthworks</h3></article>
    <article class="service-card"><div class="thumb" role="img" aria-label="Corrugated asbestos roof sheeting" style="background:linear-gradient(180deg,#6aa0d8,#9aa0a0)"></div><h3>Asbestos</h3></article>
    <article class="service-card"><div class="thumb" role="img" aria-label="Excavator digging in sunlight" style="background:linear-gradient(180deg,#4f8ed6,#c9a45a)"></div><h3>Hours of Operation</h3></article>
  </div>
</section>

<section class="welcome">
  <h1>WELCOME TO <b>VELMARSH GROUP</b></h1>
  <p>Velmarsh Transport Pty Ltd was established by Director Daniel Velmarsh in 2002 with a focus providing services within the transport industry. Over time the company has developed and expanded to include the provision of Earthworks and Demolition.</p>
  <a class="btn" href="#">READ MORE</a>
</section>

<footer class="site-footer">
  <div class="footer-col col-links">
    <h2>Useful Links</h2>
    <ul><li>Home</li><li>About</li><li>Services</li><li>Safety</li><li>Environment</li><li>Contact</li></ul>
  </div>
  <div class="footer-col col-contact">
    <h2>Conact Us</h2>
    <div class="contact-row"><svg width="16" height="18" viewBox="0 0 16 18"><path d="M8 1a6 6 0 0 0-6 6c0 4 6 10 6 10s6-6 6-10a6 6 0 0 0-6-6zm0 8.5A2.5 2.5 0 1 1 8 4.5a2.5 2.5 0 0 1 0 5z" fill="#fcfcfc"/></svg><span>PO Box 512 HARLOWE QLD 4290</span></div>
    <div class="contact-row"><svg width="18" height="18" viewBox="0 0 18 18"><path d="M4 1l3 4-2 2c1 2.5 3.5 5 6 6l2-2 4 3-2 3C8 17 1 10 1 3z" fill="#fcfcfc"/></svg><span>0400 000 118<br>0400 000 274</span></div>
    <div class="contact-row"><svg width="18" height="14" viewBox="0 0 18 14"><rect x="1" y="1" width="16" height="12" fill="none" stroke="#fcfcfc" stroke-width="1.6"/><path d="M1 1l8 7 8-7" fill="none" stroke="#fcfcfc" stroke-width="1.6"/></svg><span>vtdemolition@mailbox-example.com</span></div>
  </div>
  <div class="footer-col col-follow">
    <h2>Follow Us</h2>
    <div class="social" aria-label="Social links"><span></span><span></span><span></span></div>
    <div class="footer-brand">VELMARSH</div>
  </div>
  <div class="footer-base">© <b>VELMARSH GROUP</b> - 2015. All Rights Reserved.</div>
</footer>
</body>
</html>
```